I would like a business card to match my truck wrap and logo. I would like the font to match my existing business card please.

Industry/Entity Type

Painter

Contact Information for Business Card

Rodrigo Fenwar 801-437-2190 Fenwarcoatings.utah@brelmox.com
SERVICES - Custom Paint & Stain, Interior & Exterior, Epoxy Coatings / Garage Floors, Cabinet Refinishing, Log Staining and Refinishing.

Requirements
Nice to have
• I would like to have the white and grey line like the bottom of my vehicle wrap, Light Grey to match my truck also.

```html
<!DOCTYPE html>
<html lang="en">
<head>
<meta charset="utf-8">
<title>Fenwar Coatings – Business Card</title>
<link rel="stylesheet" href="https://fonts.googleapis.com/css2?family=Arimo:wght@400&family=Krona+One&family=Michroma&display=swap">
<style>
  :root {
    --bg: #2a2a2a;
    --blue-light: #03aaea;
    --blue-mid: #0a86d0;
    --blue-deep: #0e5ca6;
    --brand: #0aa3e4;
    --name: #0f5fa8;
    --ink: #1b1b1b;
    --divider: #9a9a9a;
    --white: #ffffff;
  }
  * { margin: 0; padding: 0; box-sizing: border-box; }
  html, body {
    width: 1200px; height: 1040px; overflow: hidden;
    background: var(--bg);
  }
  .sheet {
    position: relative; width: 1200px; height: 1040px;
  }
  .card {
    position: absolute; left: 180px; width: 840px; height: 480px;
    overflow: hidden;
  }
  /* back side */
  .card--back {
    top: 25px;
    border-radius: 110px 0 110px 0;
    background: linear-gradient(200deg, var(--blue-light) 0%, var(--blue-mid) 50%, var(--blue-deep) 100%);
    color: var(--white);
  }
  .services {
    position: absolute; left: 250px; top: 110px;
    font-family: "Michroma", sans-serif;
  }
  .services__title {
    font-family: "Krona One", sans-serif;
    font-size: 22px; letter-spacing: 1px; margin-bottom: 18px; margin-left: 22px;
  }
  .services__list { list-style: none; }
  .services__item {
    font-size: 21px; line-height: 1; margin-bottom: 20px;
    display: flex; align-items: center; gap: 10px; white-space: nowrap;
  }
  .services__item::before {
    content: ""; width: 11px; height: 11px; border-radius: 50%;
    background: var(--white); flex: none;
  }
  /* front side */
  .card--front {
    top: 535px;
    border-radius: 0 110px 0 110px;
    background: var(--white);
  }
  .brand {
    position: absolute; left: 40px; top: 0; width: 340px; height: 480px;
    display: flex; flex-direction: column; align-items: center; justify-content: center; gap: 22px;
  }
  .brand__mark { width: 44px; height: 44px; background: var(--brand); }
  .brand__name {
    font-family: "Krona One", sans-serif; font-size: 30px; line-height: 1.25;
    color: var(--brand); text-align: center; letter-spacing: 1px;
  }
  .divider {
    position: absolute; left: 405px; top: 120px; width: 1px; height: 230px;
    background: var(--divider);
  }
  .contact {
    position: absolute; left: 450px; top: 150px;
  }
  .contact__name {
    font-family: "Krona One", sans-serif; font-size: 28px; color: var(--name);
    letter-spacing: 1px; margin-bottom: 34px;
  }
  .contact__row {
    display: flex; align-items: center; gap: 10px;
    font-family: "Arimo", sans-serif; font-size: 22px; color: var(--ink);
    margin-bottom: 8px;
  }
  .contact__icon { width: 22px; height: 22px; flex: none; }
</style>
</head>
<body>
<main class="sheet">
  <section class="card card--back" aria-label="Card back: services">
    <div class="services">
      <h2 class="services__title">SERVICES</h2>
      <ul class="services__list">
        <li class="services__item">CUSTOM PAINT &amp; STAIN</li>
        <li class="services__item">INTERIOR &amp; EXTERIOR</li>
        <li class="services__item">EPOXY COATINGS / GARAGE FLOORS</li>
        <li class="services__item">CABINET REFINISHING</li>
        <li class="services__item">LOG STAINING AND REFINISHING.</li>
      </ul>
    </div>
  </section>

  <section class="card card--front" aria-label="Card front: contact">
    <div class="brand">
      <span class="brand__mark" aria-hidden="true"></span>
      <h1 class="brand__name">FENWAR<br>COATINGS</h1>
    </div>
    <div class="divider"></div>
    <div class="contact">
      <p class="contact__name">RODRIGO FENWAR</p>
      <p class="contact__row">
        <svg class="contact__icon" viewBox="0 0 24 24" aria-hidden="true">
          <path fill="var(--name)" d="M6.6 10.8a15.1 15.1 0 0 0 6.6 6.6l2.2-2.2a1 1 0 0 1 1-.25 11.4 11.4 0 0 0 3.6.57 1 1 0 0 1 1 1V20a1 1 0 0 1-1 1A17 17 0 0 1 3 4a1 1 0 0 1 1-1h3.5a1 1 0 0 1 1 1c0 1.25.2 2.45.57 3.57a1 1 0 0 1-.25 1z"/>
        </svg>
        801-437-2190
      </p>
      <p class="contact__row">
        <svg class="contact__icon" viewBox="0 0 24 24" aria-hidden="true">
          <rect x="2" y="5" width="20" height="14" fill="var(--name)"/>
          <path d="M2 5l10 8 10-8" fill="none" stroke="var(--white)" stroke-width="1.6"/>
        </svg>
        Fenwarcoatings.utah@brelmox.com
      </p>
    </div>
  </section>
</main>
</body>
</html>
```